Business Card for Professional Photographer

I'm looking for an eye catching modern clean design that compliments my logo/ website fonts & colours.
I specialise in architecture, corporate & commercial photography so I'm marketing to professional clients rather than portrait / wedding clients.

I would prefer to not have a solid black design.

My logo brand guide is as follows :

Main front font. : Reislust
Main font colour : #fff
Slogan front font : Ubuntu Bold
Monogram front font : Venti Medium
Container colour : #fff

I need print ready files in pdf .png & .eps formats.

Included in the files below are some screen grabs as reference to font & colours etc.

```html
<!DOCTYPE html>
<html lang="en">
<head>
<meta charset="utf-8">
<title>Clear Angle – Business Card</title>
<link rel="stylesheet" href="https://fonts.googleapis.com/css2?family=Montserrat:wght@500;600&display=swap">
<style>
  :root {
    --backdrop: #c9c9c9;
    --card: #ffffff;
    --gold: #b8873f;
    --grey-text: #878787;
  }
  * { box-sizing: border-box; margin: 0; padding: 0; }
  html, body { width: 1125px; height: 1200px; overflow: hidden; }
  body {
    background: var(--backdrop);
    position: relative;
    font-family: "Montserrat", sans-serif;
  }
  .card {
    position: absolute;
    left: 178px;
    width: 768px;
    height: 436px;
    background: var(--card);
    border-radius: 24px;
    overflow: hidden;
  }
  .card--front { top: 140px; }
  .card--back  { top: 626px; }

  .wordmark {
    font-family: "Montserrat", sans-serif;
    font-weight: 500;
    color: var(--gold);
    letter-spacing: 0.04em;
    white-space: nowrap;
    line-height: 1;
  }

  /* Front */
  .front-brand { position: absolute; left: 43px; top: 66px; }
  .front-brand .wordmark { font-size: 24px; }

  .person { position: absolute; left: 43px; top: 241px; }
  .person__name { font-size: 21px; font-weight: 600; color: var(--gold); line-height: 1.2; }
  .person__role { font-size: 17px; font-weight: 500; color: var(--grey-text); margin-top: 2px; }

  .contact-list { position: absolute; left: 43px; top: 314px; list-style: none; }
  .contact-list li {
    display: flex;
    align-items: center;
    height: 31.5px;
    font-size: 18px;
    font-weight: 500;
    color: var(--grey-text);
  }
  .contact-list svg { width: 13px; height: 13px; margin-right: 10px; flex: none; }

  /* Back */
  .back-mark {
    position: absolute;
    left: 170px;
    top: 194px;
    width: 48px;
    height: 48px;
    border-radius: 50%;
    background: var(--gold);
  }
  .back-brand { position: absolute; left: 240px; top: 199px; }
  .back-brand .wordmark { font-size: 38px; }
</style>
</head>
<body>

  <section class="card card--front">
    <div class="front-brand">
      <div class="wordmark">CLEAR ANGLE</div>
    </div>

    <div class="person">
      <div class="person__name">Laura Bennet</div>
      <div class="person__role">Manager</div>
    </div>

    <ul class="contact-list">
      <li>
        <svg viewBox="0 0 16 16" aria-hidden="true"><path fill="var(--gold)" d="M3.6 1.2l2.3 2.6-1.3 1.6c.8 2 2.3 3.6 4.3 4.5l1.6-1.3 2.6 2.3-1.4 2.3C6.5 13 2.9 9.4 1.3 4.2z"/></svg>
        555-012-3490
      </li>
      <li>
        <svg viewBox="0 0 16 16" aria-hidden="true"><rect x="1" y="3" width="14" height="10" fill="var(--gold)"/><path d="M2 4l6 5 6-5" fill="none" stroke="#fff" stroke-width="1.4"/></svg>
        hello@northlightstudio.com
      </li>
      <li>
        <svg viewBox="0 0 16 16" aria-hidden="true"><circle cx="8" cy="8" r="7" fill="var(--gold)"/><path d="M1 8h14M8 1c-3 3-3 11 0 14M8 1c3 3 3 11 0 14" fill="none" stroke="#fff" stroke-width="1"/></svg>
        www.northlightstudio.com
      </li>
    </ul>
  </section>

  <section class="card card--back">
    <div class="back-mark" aria-hidden="true"></div>
    <div class="back-brand">
      <div class="wordmark">CLEAR ANGLE</div>
    </div>
  </section>

</body>
</html>
```